Harborline LLC
555-418-7305
438 Walt R. Pemberton Blvd.
Lindenvale, AL 35999
harborlinellc97@quilmail.example

Heavy& Light Duty Diesel Truck, Trailer, and Equipment Repair
Certified NMC Master Tech & trained techs

Services:
alignments, brakes, suspension, A/C, engine overhauls, DOT inspections, fleet maintenance, computer diagnosis for gas & diesel, warranty work, performance parts for all diesel pickups, Welding & fabrication

Colors, text for Company, phone number, email address in bright red, all other text black.
background color of postcard light grey, black border around pictures.

Industry/Entity Type

Computer

Colors
ec2027

```html
<!DOCTYPE html>
<html lang="en">
<head>
<meta charset="utf-8">
<title>Harborline LLC Postcard</title>
<link href="https://fonts.googleapis.com/css2?family=Roboto+Condensed:ital,wght@0,700;1,700;1,800&family=Arimo:ital,wght@0,400;0,700;1,400;1,700&display=swap" rel="stylesheet">
<style>
  :root {
    --red: #ec2027;
    --ink: #111111;
    --grey-light: #e4e4e4;
    --grey-mid: #c4c4c4;
    --white: #ffffff;
    --stage: #3d3d3d;
    --photo-blue: #3a3f8f;
    --photo-shop: #9a9890;
    --photo-sky: #6f97c8;
    --photo-yard: #b9b2a2;
  }
  * { box-sizing: border-box; margin: 0; padding: 0; }
  html, body { width: 876px; height: 1200px; overflow: hidden; }
  body { background: var(--stage); position: relative; font-family: "Arimo", Arial, sans-serif; color: var(--ink); }

  .card { position: absolute; left: 62px; width: 742px; overflow: hidden; }
  .card-front { top: 12px; height: 576px; background: linear-gradient(135deg, #ededed 0%, var(--grey-light) 45%, var(--grey-mid) 100%); }
  .card-back { top: 600px; height: 592px; background: var(--white); }

  .photo { position: absolute; border: 3px solid var(--ink); border-radius: 9px; }
  .photo-truck { left: 28px; top: 54px; width: 264px; height: 344px;
    background: linear-gradient(100deg, var(--photo-blue) 0%, var(--photo-blue) 38%, var(--photo-shop) 60%, #d8d6cf 100%); }
  .photo-scanner { left: 215px; top: 314px; width: 184px; height: 146px;
    background: linear-gradient(160deg, #6b6e74 0%, #2d3036 60%, #1a1c20 100%); }

  .claims { position: absolute; left: 415px; top: 52px; width: 302px; list-style: none; }
  .claims li { position: relative; padding-left: 28px; font-family: "Roboto Condensed", Arial, sans-serif; font-style: italic; font-weight: 800; font-size: 23px; line-height: 28px; margin-bottom: 14px; text-align: justify; }
  .bullet { position: absolute; left: 0; top: 5px; width: 19px; height: 19px; border-radius: 50%; background: var(--red); }

  .section-title { position: absolute; left: 440px; font-family: "Roboto Condensed", Arial, sans-serif; font-style: italic; font-weight: 800; font-size: 25px; border-bottom: 1px solid #f7f7f7; width: 290px; padding-bottom: 2px; }
  .title-services { top: 238px; }
  .title-workshop { top: 372px; }
  .services-text { position: absolute; left: 440px; top: 278px; width: 290px; font-style: italic; font-size: 11.6px; line-height: 15.4px; text-align: justify; }
  .workshop-address { position: absolute; left: 440px; top: 412px; font-style: italic; font-weight: 700; font-size: 16.5px; line-height: 22px; }

  .contact-band { position: absolute; left: 0; top: 492px; width: 742px; height: 42px; background: var(--red); color: var(--white); display: flex; align-items: center; padding-left: 304px; }
  .band-phone { font-weight: 700; font-size: 26px; letter-spacing: 0.5px; }
  .band-divider { width: 2px; height: 30px; background: var(--white); margin: 0 10px; }
  .band-email { font-weight: 700; font-size: 14px; }

  .brand { position: absolute; background: var(--white); border-radius: 8px; display: flex; align-items: center; gap: 10px; padding-left: 12px; }
  .card-front .brand { left: 28px; top: 476px; width: 264px; height: 74px; }
  .brand-mark { width: 30px; height: 30px; background: var(--ink); flex: none; }
  .brand-name { font-family: "Arimo", Arial, sans-serif; font-weight: 700; font-size: 25px; color: var(--red); }

  .back-panel { position: absolute; left: 0; top: 20px; width: 358px; height: 454px; border-radius: 0 10px 10px 0; background: linear-gradient(135deg, #ececec 0%, var(--grey-light) 50%, var(--grey-mid) 100%); overflow: hidden; }
  .back-band { position: absolute; left: 0; top: 26px; width: 358px; height: 40px; background: var(--red); }
  .card-back .brand { left: 24px; top: 10px; width: 266px; height: 72px; }
  .photo-yard { position: absolute; left: 0; top: 68px; width: 358px; height: 118px;
    background: linear-gradient(180deg, var(--photo-sky) 0%, var(--photo-sky) 30%, #d9d6cc 50%, var(--photo-yard) 100%); }
  .back-claims { position: absolute; left: 14px; top: 206px; width: 340px; list-style: none; }
  .back-claims li { position: relative; padding-left: 22px; font-family: "Roboto Condensed", Arial, sans-serif; font-style: italic; font-weight: 700; font-size: 15.5px; line-height: 21px; margin-bottom: 10px; }
  .back-claims .bullet { width: 15px; height: 15px; top: 3px; }
  .back-contact { position: absolute; left: 20px; top: 298px; }
  .back-name { font-weight: 700; font-style: italic; font-size: 21px; color: var(--red); line-height: 28px; }
  .back-phone { font-style: italic; font-size: 25px; color: var(--red); line-height: 32px; }
  .back-address { font-style: italic; font-size: 17px; line-height: 22px; }
  .back-email { font-style: italic; font-size: 15px; color: var(--red); line-height: 26px; }

  .postage { position: absolute; left: 557px; top: 20px; width: 168px; height: 168px; border: 2px solid var(--ink); display: flex; align-items: center; justify-content: center; text-align: center; font-size: 20px; line-height: 25px; }
  .address-line { position: absolute; left: 421px; width: 286px; height: 2px; background: var(--ink); }
  .line-1 { top: 288px; }
  .line-2 { top: 321px; }
  .line-3 { top: 354px; }
  .line-4 { top: 386px; }
</style>
</head>
<body>
  <section class="card card-front">
    <div class="photo photo-truck" role="img" aria-label="Photo of a blue semi truck parked inside the repair workshop"></div>
    <div class="photo photo-scanner" role="img" aria-label="Photo of a technician holding a diagnostic scan tool"></div>

    <ul class="claims">
      <li><span class="bullet"></span>Heavy &amp; Light Duty Diesel Truck, Trailer, and Equipment Repair</li>
      <li><span class="bullet"></span>Certified NMC Master Tech &amp; trained techs</li>
    </ul>

    <h2 class="section-title title-services">Services</h2>
    <p class="services-text">Alignments, Brakes, Suspension, A/c, Engine Overhauls, Dot Inspections, Fleet Maintenance, Computer Diagnosis For Gas &amp; Diesel, Warranty Work, Performance Parts For All Diesel Pickups, Welding &amp; Fabrication</p>

    <h2 class="section-title title-workshop">Workshop</h2>
    <p class="workshop-address">438 Walt R. Pemberton Blvd.<br>Lindenvale, AL 35999</p>

    <div class="contact-band">
      <span class="band-phone">555-418-7305</span>
      <span class="band-divider"></span>
      <span class="band-email">harborlinellc97@quilmail.example</span>
    </div>
    <div class="brand"><span class="brand-mark"></span><span class="brand-name">Harborline LLC</span></div>
  </section>

  <section class="card card-back">
    <div class="back-panel">
      <div class="back-band"></div>
      <div class="brand"><span class="brand-mark"></span><span class="brand-name">Harborline LLC</span></div>
      <div class="photo-yard" role="img" aria-label="Photo of the shop building with pickup trucks parked outside"></div>
      <ul class="back-claims">
        <li><span class="bullet"></span>Heavy &amp; Light Duty Diesel Truck, Trailer, and Equipment Repair</li>
        <li><span class="bullet"></span>Certified NMC Master Tech &amp; trained techs</li>
      </ul>
      <div class="back-contact">
        <p class="back-name">Harborline LLC</p>
        <p class="back-phone">555-418-7305</p>
        <p class="back-address">438 Walt R. Pemberton Blvd.<br>Lindenvale, AL 35999</p>
        <p class="back-email">harborlinellc97@quilmail.example</p>
      </div>
    </div>

    <div class="postage">Postage<br>Area</div>
    <div class="address-line line-1"></div>
    <div class="address-line line-2"></div>
    <div class="address-line line-3"></div>
    <div class="address-line line-4"></div>
  </section>
</body>
</html>
```